Stationery Design Project

I need a stationary design for our company. we are based in Houston, TX and we are called Mira Vell Lending. And we are wanting to brand our MoneyMendPlus program, which includes our tax preparation and restoration, credit repair service. Although our business offers other programs, we are interested in mainly focusing on The MoneyMendPlus program. We are looking for way to brand our ourselves and I believe that a great stationery design will help in achieving this goal. Our logo design is blue and light blue. the slogan is orange.

Industry/Entity Type

Business

Requirements
Must have
• Address: 30871 Calloway Ln. B-22
Houston, TX 75419
Tel. 555-318-6207
Fax 555-294-7153
www.miravelllending.example
info@miravelllending.example
Our Slogan: Happiness, Restored!

```html
<!DOCTYPE html>
<html lang="en">
<head>
<meta charset="utf-8">
<title>MoneyMendPlus Business Cards</title>
<link rel="stylesheet" href="https://fonts.googleapis.com/css2?family=Tinos&family=Open+Sans:wght@400&display=swap">
<style>
  :root {
    --bg: #ecebe8;
    --white: #ffffff;
    --brand-blue: #1c5fa8;
    --deep-blue: #1a4a9a;
    --bright-blue: #0a98d8;
    --navy: #123d66;
    --pale-blue: #cde5f6;
    --gold: #e9b33a;
    --frame: #dfe7ee;
    --url-light: #d6ecfa;
  }
  * { margin: 0; padding: 0; box-sizing: border-box; }
  html, body { width: 1200px; height: 772px; overflow: hidden; }
  body { background: var(--bg); position: relative; font-family: "Open Sans", Arial, sans-serif; }

  .card {
    position: absolute;
    width: 509px;
    height: 290px;
    border-radius: 20px;
    overflow: hidden;
    box-shadow: 0 3px 8px rgba(0,0,0,0.25);
  }
  .card--front { left: 83px; top: 78px; background: var(--white); }
  .card--blue { left: 628px; top: 78px; background: linear-gradient(90deg, var(--bright-blue), var(--deep-blue)); }
  .card--pale { left: 83px; top: 403px; background: var(--pale-blue); }
  .card--white { left: 632px; top: 403px; background: var(--white); }

  .front-wave { position: absolute; inset: 0; width: 509px; height: 290px; }

  .program-name {
    position: absolute;
    left: 0; right: 0;
    text-align: center;
    font-family: "Tinos", "Times New Roman", serif;
    font-size: 44px;
    color: var(--brand-blue);
    letter-spacing: -0.5px;
  }
  .card--front .program-name { top: 56px; }
  .card--white .program-name { top: 148px; }

  .contact {
    position: absolute;
    left: 25px;
    top: 196px;
    color: var(--white);
    font-size: 12.5px;
    line-height: 18.5px;
  }
  .contact .address { margin-top: 9px; }

  .slogan {
    position: absolute;
    right: 25px;
    top: 201px;
    text-align: right;
    font-family: "Tinos", "Times New Roman", serif;
    font-size: 21px;
    line-height: 25px;
    color: var(--white);
    letter-spacing: 0.5px;
  }
  .front-url {
    position: absolute;
    right: 26px;
    top: 257px;
    color: var(--white);
    font-size: 12.5px;
  }

  .mark-box {
    position: absolute;
    left: 180px;
    top: 52px;
    width: 150px;
    height: 150px;
    background: var(--frame);
    padding: 5px;
  }
  .mark-box__inner {
    width: 100%;
    height: 100%;
    background: var(--navy);
    display: flex;
    align-items: center;
    justify-content: center;
    font-family: "Tinos", "Times New Roman", serif;
    font-size: 14px;
    color: var(--white);
    text-align: center;
  }

  .spaced-url {
    position: absolute;
    left: 0; right: 0;
    top: 240px;
    text-align: center;
    font-size: 12px;
    letter-spacing: 4.6px;
  }
  .card--blue .spaced-url { color: var(--url-light); }
  .card--pale .spaced-url, .card--white .spaced-url { color: var(--navy); }
</style>
</head>
<body>

  <section class="card card--front">
    <svg class="front-wave" viewBox="0 0 509 290" aria-hidden="true">
      <defs>
        <linearGradient id="waveBlue" x1="0" y1="0" x2="1" y2="0">
          <stop offset="0" stop-color="#2a6cc0"/>
          <stop offset="1" stop-color="#1a4a9a"/>
        </linearGradient>
      </defs>
      <path d="M0 92 Q250 300 509 108 L509 290 L0 290 Z" fill="url(#waveBlue)"/>
      <path d="M0 92 Q250 300 509 108" fill="none" stroke="var(--gold)" stroke-width="4"/>
    </svg>
    <div class="program-name">MoneyMendPlus</div>
    <div class="contact">
      <div>T: 555-318-6207</div>
      <div>F: 555-294-7153</div>
      <div>E: info@miravelllending.example</div>
      <div class="address">30871 Calloway Ln. B-22, Houston, TX 75419</div>
    </div>
    <div class="slogan">HAPPINESS,<br>RESTORED!</div>
    <div class="front-url">www.miravelllending.example</div>
  </section>

  <section class="card card--blue">
    <div class="mark-box"><div class="mark-box__inner">Mira Vell Lending</div></div>
    <div class="spaced-url">www.MiraVellLending.example</div>
  </section>

  <section class="card card--pale">
    <div class="mark-box"><div class="mark-box__inner">Mira Vell Lending</div></div>
    <div class="spaced-url">www.MiraVellLending.example</div>
  </section>

  <section class="card card--white">
    <div class="program-name">MoneyMendPlus</div>
    <div class="spaced-url">www.MiraVellLending.example</div>
  </section>

</body>
</html>
```